Design website for new email startup

We are starting a company called Pingo.QZ (it will live at http://pingo.qz).

We would like the main landing page for our site designed. We have provided a very simple wireframe to help provide direction for the content it should include, but we do not expect the designers to adhere to it at all - we encourage unique ideas. There is some sample text in the wireframe - this does not have to be used, but may provide ideas.

We provide an easy way for people to manage email for a custom domain name. For example if you own "yourhouseword.example" you can point your DNS records to us and we'll make it easy to have emails addressed to your domain get forwarded to your existing email (gmail, etc). Folks running blogs, and other small sites can quickly setup email addresses for their domains and manage them in one place.

(For technical folks, we have you point your dns mx records to us, hence the name. That way all your email hits us and we can redirect it wherever you want. We make it easy to manage a single domain or a bunch of domains. Many domain registrars offer this service for a fee, and have clumsy management tools. We provide a robust simple toolset for free, as well as premium options).

The goal of the landing page is to get folks into the signup flow. The second priority flow is to have them take a look at the premium plan offerings.

We may offer the winning designer additional work for the remainder of the site design.
Updates

I've changed this project to a committed payment.  It is no longer refundable.  Thank you.

Target Market(s)

Bloggers, podcasters, designers, app developers - people who are a little tech savvy.

Industry/Entity Type

It Company

Font styles to use
Sans Serif

Colors

Designer to choose colors to be used in the design.

Requirements
Must have
• A full fidelity mockup (comp) of the landing page including the source file (psd, ai, etc).

Some sort of logo treatment for the pingo.qz brand

A call to action for signup, such as the suggested 'Get Started Here'
Nice to have
• A hip startup feel

Incorporation of the email theme

Give the impression it is simple, easy and fast

```html
<!DOCTYPE html>
<html lang="en">
<head>
<meta charset="utf-8">
<title>Pingo.QZ – Simple email forwarding for your domain</title>
<link rel="stylesheet" href="https://fonts.googleapis.com/css2?family=Open+Sans:wght@400;600;700&display=swap">
<style>
  :root {
    --header-top: #36b1e6;
    --header-bottom: #1187cc;
    --header-line: #0a5f94;
    --brand-white: #ffffff;
    --slogan: #bfe6fa;
    --login-top: #1a6fb3;
    --login-bottom: #0b4f8a;
    --hero-light: #e4e7ea;
    --hero-mid: #dde0e3;
    --photo-dark: #2f3034;
    --photo-mid: #55575d;
    --photo-glow: rgba(255,255,255,.28);
    --title-blue: #1a84c9;
    --subtitle-blue: #22a3df;
    --body-grey: #62666c;
    --cta-blue-top: #2a96dc;
    --cta-blue-bottom: #0e6cb0;
    --cta-orange-top: #ffa01c;
    --cta-orange-bottom: #f07200;
    --card-border: #d8dadd;
    --link-navy: #1f3f8f;
    --text-small: #6a6d72;
    --footer-text: #444;
    --icon-grey: #6b6d70;
    --page: #ffffff;
  }
  * { box-sizing: border-box; margin: 0; padding: 0; }
  html, body { width: 1200px; height: 870px; overflow: hidden; }
  body {
    font-family: "Open Sans", Arial, sans-serif;
    background: radial-gradient(ellipse at 50% 85%, #ececec 0%, var(--page) 60%);
    position: relative;
  }
  .site-header {
    position: absolute; left: 0; top: 0; width: 1200px; height: 104px;
    background: linear-gradient(var(--header-top), var(--header-bottom));
    border-bottom: 1px solid var(--header-line);
  }
  .brand { position: absolute; left: 105px; top: 22px; color: var(--brand-white); }
  .brand-name { font-size: 36px; font-weight: 600; line-height: 40px; letter-spacing: -0.3px; }
  .brand-slogan { font-size: 13px; color: var(--slogan); line-height: 16px; }
  .main-nav { position: absolute; right: 106px; top: 44px; display: flex; align-items: center; gap: 35px; }
  .main-nav a { color: var(--brand-white); text-decoration: none; font-size: 16px; }
  .main-nav .login {
    background: linear-gradient(var(--login-top), var(--login-bottom));
    border-radius: 3px; font-size: 14px; padding: 6px 19px; margin-left: -10px;
  }
  .hero {
    position: absolute; left: 0; top: 105px; width: 1200px; height: 472px;
    background: linear-gradient(90deg, var(--hero-light), var(--hero-mid));
    overflow: hidden;
  }
  .hero-photo {
    position: absolute; left: 400px; top: 0; width: 800px; height: 472px;
    background:
      radial-gradient(ellipse 260px 200px at 58% 55%, var(--photo-glow), transparent 70%),
      linear-gradient(90deg, rgba(228,231,234,0) 0%, rgba(221,224,227,1) 24%, #b9bcc0 30%, var(--photo-mid) 38%, var(--photo-dark) 60%, var(--photo-mid) 100%);
  }
  .hero-copy { position: absolute; left: 107px; top: 132px; width: 540px; }
  .hero-title { font-size: 49px; font-weight: 600; color: var(--title-blue); line-height: 56px; letter-spacing: 0.3px; }
  .hero-subtitle { font-size: 24.5px; font-weight: 600; color: var(--subtitle-blue); line-height: 30px; }
  .hero-text { font-size: 14px; color: var(--body-grey); line-height: 21px; margin-top: 5px; width: 490px; }
  .hero-actions { display: flex; gap: 11px; margin-top: 16px; }
  .btn {
    display: inline-block; height: 39px; line-height: 39px; text-align: center;
    color: #fff; text-decoration: none; font-size: 15px; font-weight: 600; border-radius: 2px;
  }
  .btn-primary { width: 179px; background: linear-gradient(var(--cta-blue-top), var(--cta-blue-bottom)); }
  .btn-secondary { width: 169px; background: linear-gradient(var(--cta-orange-top), var(--cta-orange-bottom)); }
  .slider-dots { position: absolute; left: 567px; top: 458px; display: flex; gap: 4px; }
  .slider-dots span { width: 14px; height: 14px; border-radius: 50%; background: #fff; }
  .slider-dots span.active { background: #111; }
  .articles {
    position: absolute; left: 106px; top: 601px; width: 992px; height: 188px;
    border: 1px solid var(--card-border); background: #fff;
    display: flex; padding: 19px 14px 0;
  }
  .article { display: flex; width: 488px; }
  .article + .article { margin-left: 16px; }
  .article-thumb { width: 174px; height: 143px; flex: none; border: 1px solid #ccc; }
  .thumb-cloud { background: linear-gradient(135deg, #c9cdd1, #8a8f95); }
  .thumb-web { background: linear-gradient(135deg, #eaf3fb, #a9cbe8); }
  .article-body { margin-left: 12px; width: 292px; }
  .article-title { font-size: 16px; font-weight: 400; color: var(--link-navy); line-height: 22px; margin-top: -2px; }
  .article-text { font-size: 11px; color: var(--text-small); line-height: 17.5px; margin-top: 7px; width: 278px; }
  .learn-more { display: inline-block; margin-top: 8px; font-size: 12.5px; color: var(--link-navy); text-decoration: none; }
  .site-footer { position: absolute; left: 107px; top: 812px; width: 970px; display: flex; justify-content: space-between; align-items: center; }
  .copyright { font-size: 11.5px; color: var(--footer-text); }
  .social { display: flex; gap: 8px; }
  .social span { width: 24px; height: 24px; border-radius: 50%; background: var(--icon-grey); display: block; }
</style>
</head>
<body>
  <header class="site-header">
    <div class="brand">
      <div class="brand-name">Pingo.QZ</div>
      <div class="brand-slogan">Your Slogan goes here</div>
    </div>
    <nav class="main-nav">
      <a href="#">Home</a>
      <a href="#">How it Works</a>
      <a href="#">Support</a>
      <a href="#" class="login">Login</a>
    </nav>
  </header>

  <section class="hero">
    <div class="hero-photo" role="img" aria-label="Businessman in a dark suit tapping a tablet as glowing envelope icons rise from it"></div>
    <div class="hero-copy">
      <h1 class="hero-title">Duis tincidunt lectus</h1>
      <h2 class="hero-subtitle">Suspendisse vulputate aliquam</h2>
      <p class="hero-text">Duis tincidunt lectus quis dui viverra vestibulum. Suspendisse vulputate aliquam dui. Nulla elementum dui ut augue Aliquam</p>
      <div class="hero-actions">
        <a href="#" class="btn btn-primary">GET STARTED NOW</a>
        <a href="#" class="btn btn-secondary">COMPARE PLANS</a>
      </div>
    </div>
    <div class="slider-dots"><span class="active"></span><span></span><span></span><span></span></div>
  </section>

  <section class="articles">
    <article class="article">
      <div class="article-thumb thumb-cloud" role="img" aria-label="Hand touching a drawn cloud icon"></div>
      <div class="article-body">
        <h3 class="article-title">How to Configure your Cloudvane DNS to use pingo.qz</h3>
        <p class="article-text">Cum sociis natoque penatibus et magnis dis parturi-ent montes nascetur ridiculus mus. In iaculis facilisis massa. Etiam eu urna. Sed porta. Suspendisse quam leo molestie sed luctusgiat</p>
        <a href="#" class="learn-more">Learn More &raquo;</a>
      </div>
    </article>
    <article class="article">
      <div class="article-thumb thumb-web" role="img" aria-label="Browser address bar with a globe and a mouse pointer"></div>
      <div class="article-body">
        <h3 class="article-title">Use pingo.qz with your NameHarbor domain registration for reliable email forwarding</h3>
        <p class="article-text">Cum sociis natoque penatibus et magnis dis parturi-ent montes nascetur ridiculus mus. In iaculis facilisis massa. Etiam eu urna. Sed porta.</p>
        <a href="#" class="learn-more">Learn More &raquo;</a>
      </div>
    </article>
  </section>

  <footer class="site-footer">
    <p class="copyright">Copyright © 2014 Kestrel Consulting. All Rights Reserved.</p>
    <div class="social">
      <span aria-label="Social link"></span>
      <span aria-label="Social link"></span>
      <span aria-label="Social link"></span>
    </div>
  </footer>
</body>
</html>
```